To design a brand identity that is simple and creative with 'Corvane' as the brand name, I like modern simple fonts like helvetica neue, I want to print both sides of the card, I am open to dark front and white back, but the design needs to transfer well to letter heads and email signatures, I am looking for sophisticated and elegant, but open minded about clever and off the wall, I do not do 'boring' Corvane Ventures is the mother company for a small group, specialising in Management & consulting, Software development and construction, we have a high level of integrity, we are transparent and accountable for what we do. my images are provided as a guide only, Im not expecting them to be just copied, Im looking for a creator and passionate thinker, who will put life into their work.

Target Market(s)

usually business minded people who are looking for something different in me, such as leadership, confidence and focus with thinking that is per haps a little outside the box..

Industry/Entity Type

Construction

Requirements
Must have
• clean, minmalistic
Nice to have
• custom logo
Should not have
• boring, traditional

```html
<!DOCTYPE html>
<html lang="en">
<head>
<meta charset="utf-8">
<title>Corvane Ventures – Business Card</title>
<link rel="stylesheet" href="https://fonts.googleapis.com/css2?family=Inter:wght@300;400&display=swap">
<style>
  :root {
    --stage: #2f2c2a;
    --card-light: #f7f6f6;
    --card-light-shade: #ebe9e9;
    --card-dark: #2b2a2a;
    --card-dark-glow: #4a4646;
    --ink: #111111;
    --ink-soft: #222222;
    --ghost: #c4c2c2;
    --accent: #e0251b;
    --accent-soft: #e8603f;
    --white: #ffffff;
    --label: #dcdcdc;
    --mark-warm: #f2a73a;
  }
  * { margin: 0; padding: 0; box-sizing: border-box; }
  html, body { width: 1000px; height: 1200px; overflow: hidden; }
  body {
    background: var(--stage);
    font-family: "Inter", "Helvetica Neue", Arial, sans-serif;
    position: relative;
  }
  .side-label {
    position: absolute;
    color: var(--label);
    font-size: 20px;
    font-weight: 400;
  }
  .side-label--front { left: 811px; top: 569px; }
  .side-label--back { left: 117px; top: 1144px; }

  .card {
    position: absolute;
    width: 740px;
    height: 457px;
    overflow: hidden;
  }
  .card--front { left: 136px; top: 75px; background: var(--card-light); }
  .card--back {
    left: 117px; top: 651px;
    background: radial-gradient(ellipse 60% 70% at 50% 40%, var(--card-dark-glow), var(--card-dark) 75%);
  }

  .card__texture {
    position: absolute; inset: 0;
    background: linear-gradient(135deg, var(--card-light) 0%, var(--card-light-shade) 50%, var(--card-light) 100%);
  }

  .holder {
    position: absolute; right: 44px; top: 52px;
    text-align: right; color: var(--ink);
  }
  .holder__name { font-size: 25px; font-weight: 400; line-height: 1.1; }
  .holder__role { font-size: 16px; font-weight: 400; margin-top: 2px; }

  .ghost-name {
    position: absolute; left: 0; right: 0; top: 124px;
    text-align: center;
    font-size: 96px; font-weight: 300;
    color: var(--ghost); opacity: 0.7;
    letter-spacing: -1px;
  }

  .services {
    position: absolute; left: 0; right: 0;
    text-align: center;
    font-size: 15.5px; letter-spacing: 1.3px;
  }
  .services__dot {
    display: inline-block; width: 5px; height: 5px; border-radius: 50%;
    background: var(--accent); vertical-align: middle; margin: 0 9px;
  }
  .card--front .services { top: 171px; color: var(--ink); }
  .card--back .services { top: 297px; color: var(--white); }

  .contact {
    position: absolute; left: 0; right: 0;
    text-align: center; font-size: 18.5px; color: var(--ink-soft);
  }
  .contact--first { top: 239px; }
  .contact--second { top: 272px; }
  .contact__key { color: var(--accent-soft); margin-right: 4px; }
  .contact__gap { display: inline-block; width: 18px; }

  .brand { position: absolute; display: flex; align-items: center; }
  .brand__dot { border-radius: 50%; background: var(--mark-warm); }
  .brand__name { font-weight: 300; }
  .card--front .brand { left: 47px; top: 318px; gap: 18px; }
  .card--front .brand__dot { width: 52px; height: 52px; }
  .card--front .brand__name { font-size: 54px; color: var(--ink); }
  .card--back .brand { left: 0; right: 0; top: 168px; justify-content: center; gap: 22px; }
  .card--back .brand__dot { width: 110px; height: 110px; }
  .card--back .brand__name { font-size: 100px; color: var(--white); letter-spacing: -1px; }

  .web {
    position: absolute; left: 0; right: 0; top: 326px;
    text-align: center; font-size: 17px; color: var(--label);
  }
  .web__key { color: var(--accent); margin-right: 4px; }
</style>
</head>
<body>

  <section class="card card--front" aria-label="Card front">
    <div class="card__texture" role="img" aria-label="Soft white embossed geometric pattern"></div>

    <div class="holder">
      <p class="holder__name">Mira Talen</p>
      <p class="holder__role">client ambassador</p>
    </div>

    <p class="ghost-name" aria-hidden="true">corvane</p>

    <p class="services">management<span class="services__dot"></span>software<span class="services__dot"></span>construction</p>

    <p class="contact contact--first"><span class="contact__key">c.</span>+61 0400 555 019<span class="contact__gap"></span><span class="contact__key">e.</span>info@corvane.com.au</p>
    <p class="contact contact--second"><span class="contact__key">a.</span>po box 418 perth 6000</p>

    <div class="brand">
      <span class="brand__dot"></span>
      <span class="brand__name">corvane</span>
    </div>
  </section>
  <p class="side-label side-label--front">Front</p>

  <section class="card card--back" aria-label="Card back">
    <div class="brand">
      <span class="brand__dot"></span>
      <span class="brand__name">corvane</span>
    </div>
    <p class="services">management<span class="services__dot"></span>software<span class="services__dot"></span>construction</p>
    <p class="web"><span class="web__key">w.</span>www.corvane.ventures</p>
  </section>
  <p class="side-label side-label--back">Back</p>

</body>
</html>
```